Heron Loan Partners Business Card

We need a business card design for our mortgage servicing company. In addition to servicing the loans of homeowners, we help homeowners with purchasing their homes and any mortgage refinancing. We would like to see designs that use the colors in the logo attached below (gold-ish yellow and navy blue), and any other design you deem fit! The design should communicate a simpler life with smart mortgages provided by Heron.

```html
<!DOCTYPE html>
<html lang="en">
<head>
<meta charset="utf-8">
<title>Heron Loan Partners Business Card</title>
<link rel="stylesheet" href="https://fonts.googleapis.com/css2?family=Arimo:wght@400;700&display=swap">
<style>
  :root {
    --navy: #231f55;
    --gold: #e2b23a;
    --white: #ffffff;
    --ink: #1f1b4d;
    --grey: #666666;
    --rule: #cfcfcf;
    --backdrop: #3b3b3b;
  }
  * { box-sizing: border-box; margin: 0; padding: 0; }
  html, body { width: 1200px; height: 689px; overflow: hidden; }
  body {
    background: var(--backdrop);
    font-family: "Arimo", Arial, sans-serif;
    position: relative;
  }
  .card {
    position: absolute;
    top: 172px;
    width: 540px;
    height: 320px;
    border-radius: 22px;
    overflow: hidden;
    box-shadow: 0 14px 30px rgba(0,0,0,.35);
  }
  .card--front { left: 40px; background: var(--navy); }
  .card--back { left: 620px; background: var(--white); }

  .brand {
    position: absolute;
    display: flex;
    align-items: center;
    gap: 10px;
    font-weight: 700;
    color: var(--gold);
    white-space: nowrap;
  }
  .brand__mark {
    width: 12px; height: 12px;
    border-radius: 50%;
    background: var(--gold);
  }
  .card--front .brand { left: 0; right: 0; top: 112px; justify-content: center; font-size: 40px; }
  .tagline {
    position: absolute; left: 0; right: 0; top: 192px;
    text-align: center; color: var(--white); font-size: 15px;
  }

  .card--back .brand { right: 70px; top: 56px; font-size: 28px; }
  .divider {
    position: absolute; left: 40px; right: 40px; top: 132px;
    height: 1px; background: var(--rule);
  }
  .address {
    position: absolute; right: 40px; top: 144px;
    text-align: right; font-size: 14px; line-height: 20px; color: var(--grey);
  }
  .person { position: absolute; left: 40px; top: 168px; }
  .person__name { font-size: 24px; font-weight: 700; color: var(--ink); }
  .person__role { font-size: 13px; color: var(--grey); margin-top: 2px; }
  .contacts {
    position: absolute; left: 40px; top: 222px;
    list-style: none; font-size: 13px; line-height: 18px; color: #444;
    border-top: 1px solid var(--rule); padding-top: 6px; width: 230px;
  }
  .contacts li { display: flex; align-items: center; gap: 8px; white-space: nowrap; }
  .contacts svg { width: 11px; height: 11px; flex: none; }
  .footer-band { position: absolute; left: 0; bottom: 0; width: 540px; height: 60px; }
  .website {
    position: absolute; right: 24px; bottom: 12px;
    color: var(--white); font-size: 13px; white-space: nowrap;
  }
</style>
</head>
<body>
  <section class="card card--front">
    <div class="brand"><span class="brand__mark"></span>Heron Loan Partners</div>
    <p class="tagline">Simpler life with smart mortgages</p>
  </section>

  <section class="card card--back">
    <div class="brand"><span class="brand__mark"></span>Heron Loan Partners</div>
    <div class="divider"></div>
    <p class="address">412 Willow Bend Road<br>Fairview, Canada 20815</p>
    <div class="person">
      <p class="person__name">Daniel Reyes</p>
      <p class="person__role">President</p>
    </div>
    <ul class="contacts">
      <li><svg viewBox="0 0 12 12"><path d="M2 1h3l1 3-1.5 1a6 6 0 0 0 2.5 2.5L8 6l3 1v3a1 1 0 0 1-1 1A9 9 0 0 1 1 2a1 1 0 0 1 1-1z" fill="#e2b23a"/></svg>555-014-2291</li>
      <li><svg viewBox="0 0 12 12"><rect x="3" y="0.5" width="6" height="11" rx="1" fill="none" stroke="#e2b23a" stroke-width="1.2"/></svg>555-018-7730</li>
      <li><svg viewBox="0 0 12 12"><rect x="0.5" y="2" width="11" height="8" fill="#e2b23a"/><path d="M0.5 2l5.5 4.5L11.5 2" fill="none" stroke="#fff" stroke-width="1"/></svg>info@heronloanpartners.com</li>
    </ul>
    <svg class="footer-band" viewBox="0 0 540 60" aria-hidden="true">
      <path d="M0 50 H270 Q282 50 286 42 L293 27 Q297 20 310 20 H540 V60 H0 Z" fill="#231f55"/>
      <path d="M0 44 H266 Q276 44 280 37 L287 22" fill="none" stroke="#e2b23a" stroke-width="4"/>
    </svg>
    <p class="website">www.heronloanpartners.com</p>
  </section>
</body>
</html>
```